Website for Architecture & Interior Design firm

We are architecture and interior design firm looking for website design, word press based, smooth, elegant and easy to use for visitors. It should be easy to navigate using a mobile phone, with the ability to change pictures easily. It is a Bilingual website, (English: left to right, Arabic: right to left). A button in the menu bar is required to change the language, At first, we expect an English version, then we will help the designer by providing Arabic translation for any part of the website. Our website main purpose is to display our works in a picture format (Portfolio) to our clients, which mainly consist of four galleries from our (Services) as follow: 1- Architecture 2- Interior Design 3- Project Management 4- Importing from Abroad - Each service will have its page, which displays projects(items) in thumbnail format with simple text, which deploys (when clicked) into Fullscreen gallery to show the items related pictures (Dark gray or black background). - Navigation buttons/arrows are required, (X) button to close the navigation. - This is a very important part, the user experience in PC/Browser mode or Mobile mode should be easy, error-free and fast. Our homepage consists of four main elements: A- Edge to edge picture (Changing in a smooth transitional way, Random pictures from our Services) with our Logo, also persistent menu bar in the top (Home | About Us | Architecture | Interior design | Project Management | Importing from Abroad) + Social media icons B- Photo tiles (Random pictures from our Services) C- Our Services in a fixed 4-tile picture (Clickable) D- Contact Section (Simple name, contact number, message form) We expect the final service should be: 1- a fully functioning website, WordPress based, ready to be used by visitors 2- full content filling, we will contact the designer and provide the material (texture, text,etc..)
Colors
Designer to choose colors to be used in the design.
Look and feel
Each slider illustrates characteristics of the customer's brand and the style your logo design should communicate.

```html
<!DOCTYPE html>
<html lang="en">
<head>
<meta charset="utf-8">
<title>Meridian Atelier — Architecture &amp; Interior Design</title>
<link rel="stylesheet" href="https://fonts.googleapis.com/css2?family=Lato:wght@400;700;900&display=swap">
<style>
:root{
  --orange:#ff6a0d;
  --ink:#2a2a2a;
  --nav:#2b2b2b;
  --muted:#444;
  --panel:#eeeeee;
  --slate:#4e5158;
  --footer:#1d1d1f;
  --white:#ffffff;
}
*{box-sizing:border-box;margin:0;padding:0}
html,body{width:1200px;height:2769px;overflow:hidden;background:var(--white);font-family:'Lato',sans-serif;color:var(--ink)}
.page{position:relative;width:1200px;height:2769px;overflow:hidden}
.abs{position:absolute}

/* header */
.topbar{left:0;top:0;width:1200px;height:95px;background:var(--white)}
.social{display:flex;gap:18px;align-items:center}
.social span{width:16px;height:16px;border-radius:50%;background:#333;display:block}
.topbar .social{position:absolute;left:873px;top:38px}
.lang{position:absolute;left:1085px;top:37px;font-size:15px;font-weight:700;color:#333}
.lang svg{margin-left:6px;vertical-align:middle}
.navbar{left:0;top:95px;width:1200px;height:51px;background:var(--nav)}
.menu{position:absolute;left:236px;top:0;height:51px;display:flex;list-style:none}
.menu li{height:51px;line-height:51px;padding:0 17px;color:var(--white);font-size:14px;font-weight:700;letter-spacing:.2px}
.menu li.active{background:var(--orange)}
.brand{left:75px;top:30px;width:142px;height:132px;border-radius:50%;background:var(--white);display:flex;align-items:center;justify-content:center;text-align:center;z-index:3}
.brand-name{font-size:19px;font-weight:900;color:#111;line-height:1.15}

/* hero */
.hero{left:0;top:146px;width:1200px;height:630px;background:
  radial-gradient(ellipse at 70% 55%,rgba(230,150,60,.45),transparent 55%),
  radial-gradient(ellipse at 20% 70%,rgba(200,140,60,.35),transparent 50%),
  linear-gradient(180deg,#1d2230 0%,#2a3040 40%,#3c3526 100%)}
.hero-title{left:0;top:350px;width:1200px;text-align:center;color:var(--white);font-size:82px;font-weight:900;letter-spacing:1px}
.hero-sub{left:0;top:444px;width:1200px;text-align:center;color:var(--white);font-size:29px;font-weight:700;line-height:36px}
.dots{left:550px;top:686px;display:flex;gap:10px}
.dots i{width:17px;height:17px;border-radius:50%;background:var(--white);display:block}
.dots i:first-child{background:#9a9a9a}

/* welcome */
.section-title{width:1200px;left:0;text-align:center;font-size:37px;font-weight:900;color:var(--ink)}
.welcome-text{left:0;top:880px;width:1200px;text-align:center;font-size:16.5px;line-height:30.5px;color:var(--muted)}
.btn{background:var(--orange);color:var(--white);font-size:20px;font-weight:700;text-align:center;line-height:56px;width:208px;height:56px;left:497px}

/* services */
.services{left:0;top:1127px;width:1200px;height:548px;background:linear-gradient(180deg,var(--panel),#f6f6f6 60%,var(--panel))}
.card{top:1244px;width:242px;height:372px;overflow:hidden}
.card .photo{width:100%;height:100%}
.card .caption{position:absolute;left:0;bottom:0;width:100%;height:96px;background:rgba(35,35,35,.88);color:var(--white);font-size:22px;font-weight:700;display:flex;align-items:center;justify-content:center;text-align:center;line-height:26px}

/* gallery */
.gallery{left:0;top:1675px;width:1200px;height:620px;background:linear-gradient(180deg,var(--panel),#fafafa)}
.filters{left:188px;top:1792px;display:flex;align-items:center;list-style:none}
.filters li{font-size:14.5px;font-weight:700;color:#333;margin-right:46px}
.filters li.active{background:var(--orange);color:var(--white);padding:0 19px;height:36px;line-height:36px;margin-right:28px}
.tile{}

/* contact */
.contact-title{top:2342px;color:var(--white)}
.field{background:var(--white);font-size:15px;color:#333;padding:0 14px;line-height:48px}
.field.area{line-height:normal;padding-top:20px}

/* footer */
.footer{left:0;top:2705px;width:1200px;height:64px;background:var(--footer)}
.footer .copy{position:absolute;left:75px;top:24px;color:var(--white);font-size:13px}
.footer .social{position:absolute;left:962px;top:24px}
.footer .social span{background:#cfcfcf}
.footer .ver{position:absolute;left:1162px;top:30px;color:#bbb;font-size:13px}
</style>
</head>
<body>
<div class="page">

  <header>
    <div class="abs topbar">
      <div class="social" aria-label="Social links"><span></span><span></span><span></span><span></span><span></span></div>
      <div class="lang">EN<svg width="10" height="7" viewBox="0 0 10 7"><path d="M1 1l4 4 4-4" fill="none" stroke="#333" stroke-width="1.6"/></svg></div>
    </div>
    <nav class="abs navbar">
      <ul class="menu">
        <li class="active">HOME</li><li>ABOUT US</li><li>ARCHITECTURE</li><li>INTERIOR DESIGN</li><li>PROJECT MANAGEMENT</li><li>IMPORTING FROM ABROAD</li>
      </ul>
    </nav>
    <div class="abs brand"><div class="brand-name">Meridian<br>Atelier</div></div>
  </header>

  <section>
    <div class="abs hero" role="img" aria-label="Night-time city skyline with illuminated towers"></div>
    <svg class="abs" style="left:0;top:690px" width="1200" height="90" viewBox="0 690 1200 90"><path d="M0 768 Q300 700 600 762 Q900 700 1200 768 V780 H0Z" fill="#fff"/></svg>
    <h1 class="abs hero-title">MERIDIAN ATELIER</h1>
    <p class="abs hero-sub">ARCHITECTURE AND INTERIOR DESIGN FIRM<br>IN SAUDI ARABIA</p>
    <div class="abs dots"><i></i><i></i><i></i><i></i></div>
  </section>

  <section>
    <h2 class="abs section-title" style="top:820px">WELCOME TO OUR WEBSITE</h2>
    <p class="abs welcome-text">Lorem ipsum dolor sit amet, consectetur adipiscing elit. Suspendisse sapien sapien, ultricies id libero ornare, elementum egestas massa.<br>Vivamus blandit iaculis mauris eget commodo. Quisque id risus dui. Ut dignissim quam eros, vitae luctus nulla fermentum ac.<br>Donec cursus, lectus nec pulvinar blandit, metus enim porttitor leo, ac lobortis nisl turpis eu ante.</p>
    <div class="abs btn" style="top:1005px">READ MORE</div>
  </section>

  <section>
    <div class="abs services"></div>
    <h2 class="abs section-title" style="top:1167px">OUR SERVICES</h2>
    <div class="abs card" style="left:75px"><div class="photo" role="img" aria-label="Modern glass tower against blue sky" style="background:linear-gradient(160deg,#1f5fb8,#2d8fa0 60%,#274a3a)"></div><div class="caption">ARCHITECTURE</div></div>
    <div class="abs card" style="left:342px"><div class="photo" role="img" aria-label="Dark classic living room interior" style="background:linear-gradient(170deg,#3a3530,#5c5347 55%,#2a2624)"></div><div class="caption">INTERIOR DESIGN</div></div>
    <div class="abs card" style="left:614px"><div class="photo" role="img" aria-label="Hands sketching on drawing plans" style="background:linear-gradient(150deg,#d9a46a,#f0e8dc 50%,#c9b9a2)"></div><div class="caption">PROJECT<br>MANAGEMENT</div></div>
    <div class="abs card" style="left:884px"><div class="photo" role="img" aria-label="Professional working at a desk" style="background:linear-gradient(170deg,#c8d3dc,#8fb0d0 55%,#6c6a68)"></div><div class="caption">IMPORTING FROM<br>ABROAD</div></div>
  </section>

  <section>
    <div class="abs gallery"></div>
    <h2 class="abs section-title" style="top:1724px">GALLERY</h2>
    <ul class="abs filters"><li class="active">ALL</li><li>ARCHITECTURE</li><li>INTERIOR DESIGN</li><li>PROJECT MANAGEMENT</li><li>IMPORTING FROM ABROAD</li></ul>
    <div class="abs tile" style="left:75px;top:1868px;width:393px;height:307px;background:linear-gradient(170deg,#8d9db8,#6f7a8c 55%,#7a5a46)" role="img" aria-label="Angular contemporary building at dusk"></div>
    <div class="abs tile" style="left:481px;top:1868px;width:239px;height:147px;background:linear-gradient(160deg,#6a6a6a,#3f3f3f)" role="img" aria-label="Concrete-walled lounge interior"></div>
    <div class="abs tile" style="left:481px;top:2028px;width:239px;height:147px;background:linear-gradient(160deg,#4a4552,#2c2a33 60%,#7e8a9a)" role="img" aria-label="Modern living room with large windows"></div>
    <div class="abs tile" style="left:733px;top:1868px;width:393px;height:307px;background:linear-gradient(180deg,#dfe6ec,#b7b3a6 55%,#5b7a3a 80%,#6c6c6c)" role="img" aria-label="High-rise towers beside a highway"></div>
  </section>

  <section>
    <svg class="abs" style="left:0;top:2190px" width="1200" height="515" viewBox="0 2190 1200 515" role="img" aria-label="Dimmed aerial city view">
      <defs><linearGradient id="contactBg" x1="0" y1="0" x2="0" y2="1"><stop offset="0" stop-color="#56585e"/><stop offset=".6" stop-color="#4a4a50"/><stop offset="1" stop-color="#5a4a44"/></linearGradient></defs>
      <path d="M0 2288 Q300 2200 600 2280 Q900 2200 1200 2288 V2705 H0Z" fill="url(#contactBg)"/>
    </svg>
    <h2 class="abs section-title contact-title">CONTACT US</h2>
    <div class="abs field" style="left:226px;top:2417px;width:361px;height:48px">Name</div>
    <div class="abs field" style="left:613px;top:2417px;width:361px;height:48px">Contact No</div>
    <div class="abs field area" style="left:226px;top:2478px;width:748px;height:95px">Message</div>
    <div class="abs btn" style="top:2590px">SUBMIT NOW</div>
  </section>

  <footer class="abs footer">
    <div class="copy">Copyright © 2019 Company Name &nbsp;All Right Reserved</div>
    <div class="social" aria-label="Social links"><span></span><span></span><span></span><span></span><span></span></div>
    <div class="ver">X10</div>
  </footer>

</div>
</body>
</html>
```